TA BRAMLEY BUSINESS CARD DESIGN PROJECT

We need to utilize our logo that was expertly created on PixelHarbor and now need to match this with a business card design.

```html
<!DOCTYPE html>
<html lang="en">
<head>
<meta charset="utf-8">
<title>TA BRAMLEY Business Card</title>
<link href="https://fonts.googleapis.com/css2?family=Montserrat:wght@400;500;700&display=swap" rel="stylesheet">
<style>
  :root {
    --brand-blue: #0f56ad;
    --card-black: #151515;
    --card-white: #ffffff;
    --text-white: #f4f4f4;
    --backdrop: #3a3a3a;
  }
  * { box-sizing: border-box; margin: 0; padding: 0; }
  html, body { width: 1200px; height: 900px; overflow: hidden; }
  body {
    background: var(--backdrop);
    font-family: "Montserrat", sans-serif;
    display: flex;
    flex-direction: column;
    align-items: center;
    justify-content: center;
    gap: 40px;
  }
  .card {
    position: relative;
    width: 700px;
    height: 400px;
    border-radius: 24px;
    overflow: hidden;
  }
  .card-front {
    background: var(--card-white);
    display: flex;
    align-items: center;
    justify-content: center;
  }
  .front-wordmark {
    color: var(--brand-blue);
    font-weight: 700;
    font-size: 70px;
    letter-spacing: 10px;
  }
  .card-back { background: var(--card-black); }
  .wave { position: absolute; inset: 0; }
  .back-wordmark {
    position: absolute;
    left: 40px;
    top: 70px;
    color: var(--card-white);
    font-weight: 700;
    font-size: 34px;
    letter-spacing: 5px;
  }
  .identity {
    position: absolute;
    left: 60px;
    top: 262px;
  }
  .person-name {
    color: var(--brand-blue);
    font-weight: 700;
    font-size: 24px;
    letter-spacing: 1px;
  }
  .person-title {
    color: var(--text-white);
    font-size: 17px;
    margin-top: 2px;
  }
  .divider {
    position: absolute;
    left: 290px;
    right: 40px;
    top: 276px;
    height: 1.5px;
    background: var(--brand-blue);
  }
  .contact-list {
    position: absolute;
    left: 60px;
    top: 322px;
    list-style: none;
    color: var(--text-white);
    font-size: 15px;
    line-height: 22px;
  }
  .contact-list li { display: flex; align-items: center; gap: 10px; }
  .contact-list svg { width: 13px; height: 13px; fill: var(--brand-blue); flex: none; }
  .address {
    position: absolute;
    right: 40px;
    top: 292px;
    text-align: right;
    color: var(--text-white);
    font-size: 16px;
    line-height: 22px;
  }
</style>
</head>
<body>
  <section class="card card-front">
    <div class="front-wordmark">TA BRAMLEY</div>
  </section>

  <section class="card card-back">
    <svg class="wave" viewBox="0 0 700 400" aria-hidden="true">
      <path d="M0 0 H700 V0 C600 10 500 50 420 120 C330 200 220 250 0 265 Z" fill="var(--brand-blue)"/>
      <path d="M700 0 C600 10 500 50 420 120 C330 200 220 250 0 265" fill="none" stroke="var(--card-black)" stroke-width="6"/>
      <path d="M700 14 C610 24 520 62 440 132 C355 208 250 252 110 268" fill="none" stroke="var(--brand-blue)" stroke-width="3"/>
    </svg>
    <div class="back-wordmark">TA BRAMLEY</div>

    <div class="identity">
      <div class="person-name">MARCUS HALE</div>
      <div class="person-title">Managing Director</div>
    </div>
    <div class="divider"></div>

    <ul class="contact-list">
      <li><svg viewBox="0 0 24 24"><path d="M6.6 10.8a15 15 0 0 0 6.6 6.6l2.2-2.2c.3-.3.7-.4 1-.2 1.1.4 2.3.6 3.6.6.6 0 1 .4 1 1V20c0 .6-.4 1-1 1A17 17 0 0 1 3 4c0-.6.4-1 1-1h3.5c.6 0 1 .4 1 1 0 1.3.2 2.5.6 3.6.1.3 0 .7-.2 1z"/></svg>555 014 2270</li>
      <li><svg viewBox="0 0 24 24"><path d="M2 5h20v14H2z M2 5l10 8 10-8" /></svg>hello@tabramley.com</li>
      <li><svg viewBox="0 0 24 24"><circle cx="12" cy="12" r="10"/></svg>www.tabramley.com</li>
    </ul>

    <div class="address">
      74 Alder Crest Lane<br>
      Harrow Falls, GA 30990
    </div>
  </section>
</body>
</html>
```